Dental equipment company needs Black Friday email design

We are launching a black Friday/Cyber Monday sale and need a great email design to send (via Mailchimp) to our prospects. We want a bold design that hopefully has some movement to some elements. Must be able to import HTML into Mailchimp. Want to have project done by 11//22 for an 11/23 launch.

Target Market(s)

Dentists.

Requirements
Must have
• Must use our colors:
Orange - #ff6319
Teal - #56b1bf
Lt. Teal - #aed9da
Blue: #38394B
Our logo
picture of our sensor and logo (uploaded)
details of our offer.

We sell a dental x-ray sensor called VANTA. we sell it through a subscription service that costs $1,999 to sign up (one time fee) and then just $139/mo. For Black Friday/Cyber Monday we are doing a BOGO (Buy one, get one) for 50% off the sign up fee on the 2nd one (see attached image describing the sale for guidance please do not use that image, it's just there to provide clarity on the black friday/cyber monday offer ). Also, please make sure it includes that the offer expires Dec 1st 2020.

Any links on email should land on: https://www.quorvexradiant.com/sensor-shop/
Nice to have
• We would like to see some sort of movement in the email
We have some elements we use to describe our offering that could be included:
1) VANTA is GUARANTEED to work seamlessly in all major imaging software applications, including Tyrovan 9/10/11, Malbrey KTX, Fendleway, Horvani PlexCap, Quillomar, Brackenway/Whitcombe Imaging, Dorvatek Lunexa and more!

2) No Risk….try us worry free for 30 days or your money back!

3) Lifetime no-deductible warranty, support and software upgrades for PELLO Club members

```html
<!DOCTYPE html>
<html lang="en">
<head>
<meta charset="utf-8">
<title>PELLO Imaging – Black Friday Cyber Monday Sale</title>
<link rel="stylesheet" href="https://fonts.googleapis.com/css2?family=Montserrat:wght@400;500;600;700;800&display=swap">
<style>
  :root {
    --orange: #ff6319;
    --teal: #56b1bf;
    --lt-teal: #aed9da;
    --blue: #38394b;
    --ink: #111111;
    --panel-grey: #dcdcdc;
    --pill-grey: #e3e3e3;
    --white: #ffffff;
    --footer: #151515;
  }
  * { margin: 0; padding: 0; box-sizing: border-box; }
  html, body { width: 1200px; height: 3252px; overflow: hidden; }
  body {
    position: relative;
    background: var(--white);
    font-family: "Montserrat", Arial, sans-serif;
    color: var(--blue);
  }
  a { text-decoration: none; color: inherit; }

  /* Header */
  .site-header { position: absolute; top: 0; left: 0; width: 1200px; height: 148px; background: var(--white); }
  .brand { position: absolute; left: 100px; top: 22px; line-height: 1; }
  .brand-name { display: block; font-size: 64px; font-weight: 800; color: var(--blue); letter-spacing: -1px; }
  .brand-sub { display: block; font-size: 30px; font-weight: 800; color: var(--blue); margin-top: 2px; letter-spacing: 1px; }
  .social { position: absolute; right: 96px; top: 58px; display: flex; gap: 30px; }
  .social span { width: 32px; height: 32px; border-radius: 50%; background: var(--blue); display: block; }

  /* Hero */
  .hero {
    position: absolute; top: 148px; left: 0; width: 1200px; height: 712px;
    background: linear-gradient(110deg, #4a5878 0%, #6c7ea0 38%, #3d4b68 70%, #2b3550 100%);
  }
  .hero-sensor {
    position: absolute; left: 740px; top: 40px; width: 360px; height: 300px; border-radius: 40px;
    background: linear-gradient(160deg, #3a3f50, #1d2030);
  }
  .hero-title {
    position: absolute; left: 108px; top: 348px;
    color: var(--white); font-size: 66px; font-weight: 600; line-height: 1.2;
  }

  /* Subscription */
  .subscription { position: absolute; top: 860px; left: 0; width: 1200px; height: 456px; text-align: center; }
  .sub-lead { position: absolute; top: 0; width: 100%; font-size: 26px; font-weight: 500; }
  .sub-title { position: absolute; top: 34px; width: 100%; font-size: 48px; font-weight: 700; }
  .sub-pill {
    position: absolute; top: 96px; left: 415px; padding: 4px 14px;
    background: var(--pill-grey); font-size: 22px; color: #555;
  }
  .sub-price { position: absolute; top: 118px; width: 100%; font-size: 96px; font-weight: 700; color: var(--orange); }
  .sub-note { position: absolute; top: 250px; width: 100%; font-size: 20px; color: #555; }
  .btn {
    position: absolute; display: block; width: 268px; height: 74px; border-radius: 37px;
    background: var(--orange); color: var(--white); font-size: 30px; font-weight: 600;
    line-height: 74px; text-align: center;
  }
  .subscription .btn { top: 330px; left: 466px; }

  /* BOGO offer */
  .band { position: absolute; left: 0; width: 1200px; background: var(--teal); }
  .band-top { top: 1316px; height: 34px; }
  .band-bottom { top: 2080px; height: 50px; }
  .bogo { position: absolute; top: 1350px; left: 0; width: 1200px; height: 730px; background: var(--panel-grey); text-align: center; }
  .bogo-chip { position: absolute; left: 0; top: 520px; width: 68px; height: 94px; background: var(--lt-teal); }
  .bogo-title { position: absolute; top: 70px; width: 100%; font-size: 150px; font-weight: 700; color: var(--ink); line-height: 1; }
  .bogo-sub { position: absolute; top: 250px; width: 100%; font-size: 48px; font-weight: 600; color: var(--ink); }
  .bogo-deal { position: absolute; top: 330px; width: 100%; font-size: 160px; font-weight: 600; color: var(--teal); line-height: 1; }
  .bogo .btn { top: 520px; left: 466px; }
  .bogo-expiry { position: absolute; top: 624px; width: 100%; font-size: 22px; font-weight: 500; color: var(--ink); }

  /* Our offer */
  .offer-heading { position: absolute; top: 2168px; width: 1200px; text-align: center; font-size: 58px; font-weight: 600; color: var(--ink); }
  .card { position: absolute; color: var(--white); }
  .card-guarantee { left: 80px; top: 2292px; width: 500px; height: 780px; background: var(--teal); padding: 0 48px; }
  .product-name { margin-top: 70px; text-align: center; font-size: 104px; font-weight: 800; color: var(--blue); letter-spacing: 6px; line-height: 1; }
  .card-guarantee h3 { margin-top: 80px; font-size: 50px; font-weight: 700; line-height: 1.15; }
  .card-guarantee p { margin-top: 30px; font-size: 19px; font-weight: 500; line-height: 1.75; }
  .card-risk { left: 604px; top: 2292px; width: 512px; height: 308px; background: var(--blue); padding: 54px 64px; }
  .card-risk h3 { font-size: 50px; font-weight: 600; }
  .card-risk p { margin-top: 20px; font-size: 19px; font-weight: 500; line-height: 1.8; }
  .card-warranty { left: 604px; top: 2620px; width: 512px; height: 452px; background: var(--orange); padding: 54px 64px; }
  .card-warranty h3 { font-size: 50px; font-weight: 700; line-height: 1.15; }
  .card-warranty p { margin-top: 20px; font-size: 19px; font-weight: 500; line-height: 1.8; }

  /* Footer */
  .site-footer {
    position: absolute; top: 3160px; left: 0; width: 1200px; height: 92px; background: var(--footer);
    color: var(--white); text-align: center; font-size: 22px; font-weight: 500; line-height: 92px;
  }
</style>
</head>
<body>
  <header class="site-header">
    <div class="brand"><span class="brand-name">PELLO</span><span class="brand-sub">IMAGING</span></div>
    <nav class="social" aria-label="Social links"><span></span><span></span><span></span><span></span></nav>
  </header>

  <section class="hero">
    <div class="hero-bg" role="img" aria-label="Photo of a dental treatment room with the VANTA x-ray sensor"></div>
    <div class="hero-sensor" role="img" aria-label="VANTA dental x-ray sensor"></div>
    <h1 class="hero-title">Black Friday<br>Cyber Monday sale</h1>
  </section>

  <section class="subscription">
    <p class="sub-lead">We sell it through</p>
    <h2 class="sub-title">A Subscription service</h2>
    <span class="sub-pill">that costs</span>
    <p class="sub-price">$1,999</p>
    <p class="sub-note">(one time fee) and then just $139/mo</p>
    <a class="btn" href="https://www.quorvexradiant.com/sensor-shop/">Sign Up</a>
  </section>

  <div class="band band-top"></div>
  <section class="bogo">
    <div class="bogo-chip"></div>
    <h2 class="bogo-title">BOGO</h2>
    <p class="bogo-sub">(Buy one, get one)</p>
    <p class="bogo-deal">50% offer</p>
    <a class="btn" href="https://www.quorvexradiant.com/sensor-shop/">Sign Up</a>
    <p class="bogo-expiry">The offer expires Dec 1st 2020.</p>
  </section>
  <div class="band band-bottom"></div>

  <h2 class="offer-heading">Our offer</h2>

  <article class="card card-guarantee">
    <div class="product-name">VANTA</div>
    <h3>VANTA is<br>GUARANTEED</h3>
    <p>to work seamlessly in all major imaging software applications, including Tyrovan 9/10/11, Malbrey KTX, Fendleway, Horvani PlexCap, Quillomar, Brackenway/Whitcombe Imaging, Dorvatek Lunexa and more!</p>
  </article>

  <article class="card card-risk">
    <h3>No Risk</h3>
    <p>try us worry free for 30 days or your money back!</p>
  </article>

  <article class="card card-warranty">
    <h3>Lifetime no-deductible warranty,</h3>
    <p>support and software upgrades for PELLO Club members</p>
  </article>

  <footer class="site-footer">© 2020 &nbsp;|&nbsp; www.companyname.com</footer>
</body>
</html>
```